CBD AgriBusiness Verdant Trophy Business Card

We are HiTec producer of medical cannabis CBD Switzerland of high quality. Our website is alpinleaf.net, we will also revisit it graphically, the winner of this contest will be the graphic designer chosen for the new design of the website. We stand out by the skill of the team, many of our engineers we win cup cannabis. I join the current map to take as an example but to revisit completely: deletion of surname and first name, modification of funds (front / back), reorganization of text info, highlighting the address of the website. three characteristics define the business card: Professional, Class, refined. The business card must be optimized for soft-touch and selective varnish printing.

Target Market(s)

Customers and Suppliers

Industry/Entity Type

Agribusiness

Contact Information for Business Card

Logo, Tél / Whatsapp, mail, url du site : alpinleaf.net

Font styles to use
Sans Serif

Requirements
Must have
• Logo of alpinleaf.net
Nice to have
• a design that stands out well on the selective varnish
Should not have
• Last name and first name

```html
<!DOCTYPE html>
<html lang="en">
<head>
<meta charset="utf-8">
<title>alpinleaf business card</title>
<link href="https://fonts.googleapis.com/css2?family=Lato:wght@400;700&display=swap" rel="stylesheet">
<style>
  :root {
    --backdrop: #3a3431;
    --card: #0d0d0d;
    --leaf-green: #7cc35a;
    --text-light: #e9e9e9;
    --rule: #3a3a3a;
  }
  * { margin: 0; padding: 0; box-sizing: border-box; }
  html, body {
    width: 1200px; height: 844px; overflow: hidden;
    background: var(--backdrop);
    font-family: "Lato", Arial, sans-serif;
  }
  .card-set {
    position: absolute; inset: 0;
    display: flex; align-items: center; justify-content: center; gap: 60px;
  }
  .card {
    width: 500px; height: 286px;
    background: var(--card);
    border-radius: 4px;
    box-shadow: 0 10px 30px rgba(0,0,0,.45);
    position: relative;
  }
  .card-front {
    display: flex; flex-direction: column; align-items: center; justify-content: center;
  }
  .brand {
    font-weight: 700; letter-spacing: .5px;
    display: flex; align-items: center; gap: 10px;
  }
  .card-front .brand { color: var(--leaf-green); font-size: 44px; }
  .card-back .brand { color: var(--text-light); font-size: 40px; }
  .brand-mark {
    width: 22px; height: 22px; background: currentColor; display: inline-block;
  }
  .card-back {
    display: flex; align-items: center; justify-content: center;
  }
  .rule {
    width: 240px; height: 1px; background: var(--rule); margin: 14px 0;
  }
  .contact-icons { display: flex; gap: 6px; }
  .contact-icon {
    width: 22px; height: 22px; background: var(--leaf-green);
    display: flex; align-items: center; justify-content: center;
  }
  .contact-list {
    list-style: none; text-align: center; color: var(--text-light);
    font-size: 16px; line-height: 1.35;
  }
  .contact-list .website { font-weight: 700; }
</style>
</head>
<body>
  <main class="card-set">
    <section class="card card-front">
      <div class="brand"><span class="brand-mark"></span>alpinleaf</div>
      <div class="rule"></div>
      <div class="contact-icons">
        <span class="contact-icon">
          <svg width="14" height="14" viewBox="0 0 24 24" aria-hidden="true"><path fill="#0d0d0d" d="M6.6 10.8a15.2 15.2 0 0 0 6.6 6.6l2.2-2.2c.3-.3.7-.4 1-.2 1.1.4 2.3.6 3.6.6.6 0 1 .4 1 1V20c0 .6-.4 1-1 1C10.6 21 3 13.4 3 4c0-.6.4-1 1-1h3.5c.6 0 1 .4 1 1 0 1.3.2 2.5.6 3.6.1.3 0 .7-.2 1z"/></svg>
        </span>
        <span class="contact-icon">
          <svg width="14" height="14" viewBox="0 0 24 24" aria-hidden="true"><rect x="2" y="5" width="20" height="14" fill="none" stroke="#0d0d0d" stroke-width="2"/><path d="M2 5l10 8 10-8" fill="none" stroke="#0d0d0d" stroke-width="2"/></svg>
        </span>
        <span class="contact-icon">
          <svg width="14" height="14" viewBox="0 0 24 24" aria-hidden="true"><circle cx="12" cy="12" r="9" fill="none" stroke="#0d0d0d" stroke-width="2"/><path d="M3 12h18M12 3c3 3 3 15 0 18M12 3c-3 3-3 15 0 18" fill="none" stroke="#0d0d0d" stroke-width="1.6"/></svg>
        </span>
      </div>
      <div class="rule"></div>
      <ul class="contact-list">
        <li>+41 79 555 41 20</li>
        <li>office@alpinleaf.net</li>
        <li class="website">www.alpinleaf.net</li>
      </ul>
    </section>
    <section class="card card-back">
      <div class="brand"><span class="brand-mark"></span>alpinleaf</div>
    </section>
  </main>
</body>
</html>
```